Business Card Design for company

We want new business cards. We'd like something different-- yet still highly professional. Our tagline is Providing leadership, delivering success. Stock photos are ok, as long as they are relevant and look upscale.

Target Market(s)

Architecture/Business Management Consulting/Engineering Consulting

Contact Information for Business Card

dark gray background with pops of blue might be good, but you tell me. You're the designers. Rounded corners might be nice, but again, you tell me.

Font styles to use
Serif
Sans Serif

Colors
3276b5
5c5c5c
9d9d9d
fbfbfb

Requirements
Nice to have
• Something different, but still very professional.

```html
<!DOCTYPE html>
<html lang="en">
<head>
<meta charset="utf-8">
<title>Veltor Group – Business Cards</title>
<link rel="stylesheet" href="https://fonts.googleapis.com/css2?family=Work+Sans:wght@400;500&display=swap">
<style>
  :root {
    --brand-blue: #3276b5;
    --card-blue: #2f78c0;
    --map-blue: #4a8fd2;
    --ink-dark: #5c5c5c;
    --ink-light: #9d9d9d;
    --paper: #fbfbfb;
    --backdrop: #35302d;
    --white: #ffffff;
  }
  * { box-sizing: border-box; margin: 0; padding: 0; }
  html, body {
    width: 1200px; height: 716px; overflow: hidden;
    background: var(--backdrop);
    font-family: "Work Sans", Arial, sans-serif;
  }
  .sheet {
    position: relative; width: 1200px; height: 716px;
    display: flex; align-items: center; justify-content: center; gap: 40px;
  }
  .card {
    position: relative; width: 540px; height: 310px; overflow: hidden;
  }

  /* Front */
  .card-front { background: var(--card-blue); color: var(--white); }
  .world-map {
    position: absolute; left: 70px; top: 30px; width: 440px; height: 250px;
    background: radial-gradient(ellipse at 50% 50%, var(--map-blue) 0%, rgba(74,143,210,0.35) 55%, rgba(74,143,210,0) 75%);
    opacity: 0.7;
  }
  .front-brand {
    position: absolute; left: 80px; top: 70px;
  }
  .front-name {
    font-weight: 500; font-size: 58px; letter-spacing: 2px; line-height: 1;
    color: var(--white);
  }
  .front-sub {
    font-weight: 500; font-size: 24px; letter-spacing: 3px; margin-top: 6px;
    color: var(--white);
  }
  .tagline {
    position: absolute; left: 80px; top: 205px;
    font-size: 12px; letter-spacing: 1.6px; text-transform: uppercase; font-weight: 400;
  }

  /* Back */
  .card-back { background: var(--paper); color: var(--ink-dark); }
  .back-brand { position: absolute; left: 40px; top: 36px; color: var(--brand-blue); }
  .back-name { font-weight: 500; font-size: 40px; letter-spacing: 1px; line-height: 1; }
  .back-sub { font-weight: 500; font-size: 17px; letter-spacing: 2.5px; margin-top: 4px; }
  .divider {
    position: absolute; left: 40px; right: 70px; top: 128px; height: 1px;
    background: var(--brand-blue);
  }
  .contact-list {
    position: absolute; left: 40px; top: 146px; list-style: none;
    font-size: 12.5px; line-height: 17px; color: var(--ink-light);
  }
  .contact-list li { display: flex; align-items: center; gap: 8px; }
  .contact-list svg { width: 10px; height: 10px; fill: var(--brand-blue); flex: none; }
  .person {
    position: absolute; right: 36px; top: 168px; text-align: right;
  }
  .person-name {
    font-size: 20px; letter-spacing: 2px; color: var(--brand-blue); text-transform: uppercase;
  }
  .person-role { font-size: 12.5px; color: var(--ink-dark); margin-top: 2px; }
  .services {
    font-size: 12.5px; font-weight: 500; color: var(--ink-dark); line-height: 16px; margin-top: 6px;
  }
  .address { font-size: 12.5px; color: var(--ink-light); line-height: 16px; margin-top: 4px; }
</style>
</head>
<body>
<main class="sheet">
  <section class="card card-front">
    <div class="world-map" role="img" aria-label="Dotted world map in light blue"></div>
    <div class="front-brand">
      <div class="front-name">VELTOR</div>
      <div class="front-sub">GROUP</div>
    </div>
    <p class="tagline">Providing Leadership | Delivering Success</p>
  </section>

  <section class="card card-back">
    <div class="back-brand">
      <div class="back-name">VELTOR</div>
      <div class="back-sub">GROUP</div>
    </div>
    <div class="divider"></div>
    <ul class="contact-list">
      <li><svg viewBox="0 0 10 10"><rect x="2.5" y="0" width="5" height="10" rx="1"/></svg>555-201-4478</li>
      <li><svg viewBox="0 0 10 10"><path d="M2 0h2l1 3-1.5 1a6 6 0 0 0 2.5 2.5L7 5l3 1v2c0 1-1 2-2 2A8 8 0 0 1 0 2c0-1 1-2 2-2z"/></svg>01632 960412 (Oakridge)</li>
      <li><svg viewBox="0 0 10 10"><path d="M2 0h2l1 3-1.5 1a6 6 0 0 0 2.5 2.5L7 5l3 1v2c0 1-1 2-2 2A8 8 0 0 1 0 2c0-1 1-2 2-2z"/></svg>01632 960587 (Millbrook)</li>
      <li><svg viewBox="0 0 10 10"><path d="M0 2h10v6H0z M0 2l5 3.5L10 2" /></svg>info@veltorgroup.example</li>
      <li><svg viewBox="0 0 10 10"><circle cx="5" cy="5" r="5"/></svg>www.veltorgroup.example</li>
    </ul>
    <div class="person">
      <div class="person-name">Daniel Hartley</div>
      <div class="person-role">Founder</div>
      <div class="services">Architecture/Business Management<br>Consulting/Engineering Consulting</div>
      <div class="address">Unit 8, The Fenwick Centre,<br>Elmfield Park, Oakridge,<br>Wessex OK4 2ZT</div>
    </div>
  </section>
</main>
</body>
</html>
```